Quorimo Business Card Design Project

We need a business card design for quorimo.example a company based in Berlin, Germany.

?Quorimo is marketplace that enables people all over the world to monetize and exchange their individual knowledge and language skills through interactive video sessions. User are matched by their interests.

On Quorimo everybody can be student or teacher (seller or buyer).

We would love to see designs that use or main color blue and green. The design should communicate what Quorimo enables - see my notice above.

Looking so forward to your designs
Cheers from Berlin,
Lorenz

Target Market(s)

globally

Industry/Entity Type

Teacher

Requirements
Must have
• Lorenz Hubeck
CEO
Quorimo.example

Quorimo e-Services GmbH
Lindenweg 87
10247 Berlin

Fon: +49 30 418 906 25 17
Mobile: 49 172 54 91 37 6
E-Mail: l.hubeck@quorimo.example
Web: www.quorimo.example

```html
<!DOCTYPE html>
<html lang="en">
<head>
<meta charset="utf-8">
<title>Quorimo – Business Card</title>
<link href="https://fonts.googleapis.com/css2?family=Open+Sans:wght@400;700&display=swap" rel="stylesheet">
<style>
  :root {
    --page: #e9e6e1;
    --card: #ffffff;
    --ink: #3e3a33;
    --icon: #d8cd9f;
    --grey: #8a8a8a;
    --blue: #1a9ad6;
    --green: #8cbf1f;
  }
  * { margin: 0; padding: 0; box-sizing: border-box; }
  html, body {
    width: 1012px; height: 1200px; overflow: hidden;
    background: var(--page);
    font-family: "Open Sans", Arial, sans-serif;
  }
  .card {
    position: absolute; left: 184px; width: 651px; height: 456px;
    background: var(--card);
    box-shadow: 0 3px 10px rgba(0,0,0,.18);
    overflow: hidden;
  }
  .card--front { top: 93px; }
  .card--back { top: 649px; }
  .ink-band {
    position: absolute; left: 0; right: 0;
    background: linear-gradient(to bottom,
      rgba(62,58,51,0) 0%, rgba(62,58,51,.55) 14%, var(--ink) 26%,
      var(--ink) 70%, rgba(62,58,51,.55) 84%, rgba(62,58,51,0) 100%);
  }
  .card--front .ink-band { top: 34px; height: 360px; }
  .card--back .ink-band { top: 40px; height: 370px; }

  .brand { position: absolute; left: 36px; top: 146px; }
  .brand__name {
    display: flex; align-items: center; gap: 16px;
    font-size: 70px; font-weight: 400; line-height: 1; color: var(--grey);
    letter-spacing: 1px;
  }
  .brand__mark { width: 58px; height: 58px; background: var(--blue); }
  .brand__tagline {
    margin-top: 6px; margin-left: 142px;
    font-size: 22px; font-weight: 700; color: var(--blue);
    letter-spacing: 3.6px; white-space: nowrap;
  }

  .person { position: absolute; left: 406px; top: 6px; font-weight: 700; }
  .person__name { font-size: 18px; color: var(--green); line-height: 1.2; }
  .person__row { display: flex; gap: 8px; align-items: flex-start; }
  .person__role { font-size: 18px; color: var(--green); line-height: 1.2; }
  .person__company { font-size: 13px; color: var(--blue); line-height: 1.35; margin-top: 2px; }

  .contacts {
    position: absolute; left: 0; right: 0; top: 140px;
    display: flex; justify-content: space-between; padding: 0 10px 0 12px;
  }
  .contact { display: flex; flex-direction: column; align-items: center; gap: 14px; }
  .contact svg { width: 70px; height: 70px; fill: var(--icon); }
  .contact__text { font-size: 13px; font-weight: 700; color: var(--icon); white-space: nowrap; }
</style>
</head>
<body>

<section class="card card--front">
  <div class="ink-band" role="img" aria-label="Dark ink splatter band across the card"></div>
  <div class="brand">
    <div class="brand__name"><span class="brand__mark"></span>Quorimo</div>
    <div class="brand__tagline">the learning globe</div>
  </div>
</section>

<section class="card card--back">
  <div class="ink-band" role="img" aria-label="Dark ink splatter band across the card"></div>

  <div class="person">
    <div class="person__name">Lorenz Hubeck</div>
    <div class="person__row">
      <div class="person__role">CEO</div>
      <div class="person__company">Quorimo e-Services GmbH<br>Lindenweg 87<br>10247 Berlin</div>
    </div>
  </div>

  <div class="contacts">
    <div class="contact">
      <svg viewBox="0 0 64 64" aria-hidden="true">
        <path d="M14 6c3-2 6-1 8 2l6 10c1 3 0 5-2 7l-4 3c3 7 8 13 15 17l3-4c2-2 5-3 7-1l10 6c3 2 3 5 1 8l-4 5c-3 3-8 4-13 1C27 52 14 38 9 22c-2-5-1-9 2-12z"/>
      </svg>
      <span class="contact__text">+49 30 418 906 25 17</span>
    </div>
    <div class="contact">
      <svg viewBox="0 0 64 64" aria-hidden="true">
        <path d="M4 22c0-8 12-12 28-12s28 4 28 12v4c0 2-2 3-4 3h-8c-2 0-3-1-3-3v-4c-4-1-8-2-13-2s-9 1-13 2v4c0 2-1 3-3 3H8c-2 0-4-1-4-3z"/>
        <path d="M20 28h24l10 20v8c0 2-1 3-3 3H13c-2 0-3-1-3-3v-8z"/>
        <circle cx="32" cy="44" r="7" fill="#3e3a33"/>
      </svg>
      <span class="contact__text">49 172 54 91 37 6</span>
    </div>
    <div class="contact">
      <svg viewBox="0 0 64 64" aria-hidden="true">
        <path d="M4 26 32 6l28 20v32H4z"/>
        <rect x="14" y="16" width="36" height="26" fill="#ffffff"/>
        <rect x="20" y="22" width="24" height="3" fill="#3e3a33"/>
        <rect x="20" y="28" width="24" height="3" fill="#3e3a33"/>
        <path d="M4 28 32 48 60 28v4L32 52 4 32z" fill="#3e3a33"/>
      </svg>
      <span class="contact__text">l.hubeck@quorimo.example</span>
    </div>
    <div class="contact">
      <svg viewBox="0 0 64 64" aria-hidden="true">
        <circle cx="32" cy="32" r="28"/>
        <g fill="none" stroke="#3e3a33" stroke-width="2.5">
          <ellipse cx="32" cy="32" rx="12" ry="28"/>
          <line x1="32" y1="4" x2="32" y2="60"/>
          <line x1="4" y1="32" x2="60" y2="32"/>
          <path d="M9 18h46M9 46h46"/>
        </g>
      </svg>
      <span class="contact__text">www.quorimo.example</span>
    </div>
  </div>
</section>

</body>
</html>
```